WP website design Pellow - Brantz (Contest)

We need a wordpress design that will incorporate a professional color scheme with company logo in a clean layout. The design needs to consider that this will be developed on a responsive theme. Colors are red and black of the logo and and an accent color. Client wants a 'modern' look.

Industry/Entity Type

It Company

Font styles to use
Serif
Sans Serif

Colors

Designer to choose colors to be used in the design.

Requirements
Must have
• Must Have:
- Navigation: 1) Home; 2) Auctions; 3) Real Estate Listings 4) Assets For Sale 5) Services 6) About Us 7) Contact Us

Site will have slideshow - image is attached. Colors will be those in the logo, red and black with maybe an accent color. A site the client mentions liking is Mubrelbids.com for the use of color and layout.

Widgets: Featured Auctions, 2) Email signup form; 3) Testimonials blog widget; 5) Featured Video; Footer will have affiliation logo and contact info.

Home page content:
We are a family owned and operated business with over 25 years of real estate experience in Clinton and surrounding areas in Western Oklahoma. We know that purchasing a home is one of the most important decisions a person can make, and we strive to make it a successful and enjoyable experience for you!
Enjoy our website and please call if you have any questions or would like to make an appointment to view property!
Also, take a moment to look at our Auction Calendar for upcoming auction dates. Auctions are a great opportunity for great deals and rare finds, not to mention A LOT OF FUN!!

Widgets: 1) Featured Properties; 2) Call to action for Sellers 3) Testimonials blog/widget
Nice to have
• use of dropdown menus

```html
<!DOCTYPE html>
<html lang="en">
<head>
<meta charset="utf-8">
<title>Pellow Auction &amp; Real Estate</title>
<link rel="stylesheet" href="https://fonts.googleapis.com/css2?family=PT+Sans:ital,wght@0,400;0,700;1,400&family=Arimo:wght@400;700&family=Cousine:wght@400;700&display=swap">
<style>
:root{
  --brand-red:#c6203a;
  --deep-red:#a81a30;
  --accent-red:#c41424;
  --ink:#1c1c1c;
  --nav-dark:#1e1e1e;
  --panel:#e2e2e2;
  --panel-line:#b9b9b9;
  --white:#ffffff;
  --text:#222222;
}
*{margin:0;padding:0;box-sizing:border-box}
html,body{width:758px;height:1200px;overflow:hidden}
body{background:var(--brand-red);font-family:"PT Sans",sans-serif;color:var(--text);position:relative}
.page{position:absolute;left:63px;top:14px;width:631px;height:1056px;background:var(--white)}
.abs{position:absolute}
.brand{left:0;top:0;width:631px;height:83px;display:flex;align-items:center;justify-content:center}
.brand-name{font-family:"PT Sans",sans-serif;font-weight:700;font-size:30px;color:var(--accent-red);letter-spacing:1px;display:flex;align-items:center;gap:8px}
.brand-name .mark{width:14px;height:14px;background:var(--accent-red)}
.nav{left:0;top:83px;width:631px;height:31px;background:var(--nav-dark);display:flex}
.nav a{color:#fff;text-decoration:none;font-size:10.5px;display:flex;align-items:center;justify-content:center;border-right:1px solid #3a3a3a;height:31px}
.nav a.active{background:var(--accent-red)}
.hero{left:0;top:114px;width:631px;height:186px;background:linear-gradient(180deg,#7d9a62 0%,#5f7e3e 55%,#8a8a5a 100%)}
.hero-sign{left:325px;top:30px;width:186px;height:145px;background:#eeeeea}
.dropdown{left:61px;top:114px;width:125px;height:50px;background:#111;border-bottom:3px solid var(--accent-red)}
.dropdown div{height:22px;font-size:9.5px;color:#fff;padding:4px 6px}
.dropdown .first{background:var(--accent-red)}
.welcome{left:16px;top:326px;font-style:italic;font-size:17px;color:var(--accent-red)}
.intro{left:17px;top:356px;width:400px;font-size:9.6px;line-height:14px}
.intro p{margin-bottom:14px}
.card{left:12px;width:409px;height:201px;background:var(--panel);border:1px solid var(--panel-line);border-radius:3px}
.card-head{height:29px;background:linear-gradient(#2a2a2a,#0c0c0c);color:#fff;font-family:"Arimo",sans-serif;font-weight:700;font-size:10.5px;padding:8px 10px;border-radius:3px 3px 0 0}
.card-photo{left:13px;top:42px;width:182px;height:109px;background:linear-gradient(180deg,#aab3b8 0%,#c9c4bb 45%,#6d8a48 70%,#5a7a36 100%);border:1px solid #999}
.btn{top:167px;width:65px;height:21px;background:var(--accent-red);border-radius:3px;color:#fff;font-family:"Arimo",sans-serif;font-size:8.5px;display:flex;align-items:center;justify-content:center;gap:5px}
.btn i{width:10px;height:9px;background:#fff;border-radius:1px;display:block}
.card-info{left:213px;top:38px;width:190px;font-family:"Arimo",sans-serif}
.card-date{font-weight:700;font-size:12px;line-height:14px;color:#111;width:160px}
.card-desc{font-size:8px;line-height:11px;margin-top:6px;width:178px}
.card-bill{font-size:9px;font-weight:700;color:var(--accent-red);text-align:right;margin-top:7px}
.mono{font-family:"Cousine",monospace;font-size:8px;line-height:12.2px;margin-top:3px}
.mono b{font-weight:700}
.pin{display:inline-block;vertical-align:-1px;margin-right:3px}
.powered{left:170px;top:972px;width:122px;height:39px;border:1px solid #ccc;border-radius:3px;font-family:"Arimo",sans-serif;font-size:9px;color:#335;display:flex;align-items:center;justify-content:center;font-weight:700}
.widget{left:435px;width:190px;background:var(--panel);border:1px solid var(--panel-line);border-radius:3px}
.widget-head{height:28px;background:var(--accent-red);color:#fff;font-size:14px;padding:5px 12px;border-radius:3px 3px 0 0}
.signup-copy{font-size:9px;line-height:12px;padding:8px 12px 0}
.signup-input{margin:6px 0 0 12px;width:155px;height:21px;background:#fff;font-size:8.5px;color:#777;padding:5px 8px}
.signup-btn{margin:9px 0 0 13px;width:69px;height:20px;background:#111;color:#fff;font-size:10px;font-weight:700;display:flex;align-items:center;justify-content:center}
.feat-title{font-family:"Arimo",sans-serif;font-size:8.8px;font-weight:700;text-align:center;line-height:14px;margin-top:10px;letter-spacing:.3px}
.feat-map{margin:10px auto 0;width:96px;height:100px;background:linear-gradient(135deg,#3e5a2c,#6b8a4a 60%,#2f4620);border:2px solid #9c1a22}
.feat-cap{font-family:"Arimo",sans-serif;font-size:7.2px;text-align:center;line-height:10px;margin-top:11px}
.video{left:436px;top:756px;width:188px;height:131px;background:#111;padding:3px}
.video-frame{width:100%;height:113px;background:linear-gradient(160deg,#7a8ea0 0%,#5a4a42 50%,#2c2c30 100%);display:flex;align-items:center;justify-content:center}
.testimonial{left:435px;top:906px;width:190px;height:134px;background:var(--nav-dark);border-radius:4px;color:#fff;font-family:"Arimo",sans-serif;padding:12px 13px}
.testimonial h3{font-size:9.5px;font-weight:700}
.testimonial p{font-size:8px;line-height:11.5px;margin-top:8px}
.testimonial .more{font-size:8px;font-weight:700;margin-top:11px}
.footer-contact{left:71px;top:1083px;color:#fff;font-family:"Arimo",sans-serif;font-size:8.6px;line-height:12.7px}
.badge{background:#fff;position:absolute}
.footer-copy{left:71px;top:1176px;color:#fff;font-family:"Arimo",sans-serif;font-size:7.3px}
.footer-powered{left:511px;top:1176px;color:#fff;font-family:"Arimo",sans-serif;font-size:7.3px}
</style>
</head>
<body>
<div class="page">
  <div class="abs brand"><span class="brand-name"><span class="mark"></span>PELLOW</span></div>

  <nav class="abs nav">
    <a style="width:61px">HOME</a>
    <a class="active" style="width:81px">AUCTIONS</a>
    <a style="width:132px">REAL ESTATE LISTINGS</a>
    <a style="width:110px">ASSETS FOR SALE</a>
    <a style="width:75px">SERVICES</a>
    <a style="width:81px">ABOUT US</a>
    <a style="width:91px;border-right:0">CONTACT US</a>
  </nav>

  <div class="abs hero" role="img" aria-label="Slideshow photo: auction sign on a fence beside a grassy field">
    <div class="abs hero-sign" role="img" aria-label="Roadside auction sign"></div>
  </div>

  <div class="abs dropdown">
    <div class="first">Upcoming auctions</div>
    <div>Past auctions</div>
  </div>

  <h1 class="abs welcome" style="font-weight:400">Welcome to Pellow Auction &amp; Real Estate!</h1>
  <div class="abs intro">
    <p>We are a family owned and operated business with over 25 years of real estate experience in Clinton and surrounding areas in Western Oklahoma. We know that purchasing a home is one of the most important decisions a person can make, and we strive to make it a successful and enjoyable experience for you!</p>
    <p>Enjoy our website and please call if you have any questions or would like to make an appointment to view property!</p>
    <p>Also, take a moment to look at our Auction Calendar for upcoming auction dates. Auctions are a great opportunity for great deals and rare finds, not to mention A LOT OF FUN!!</p>
  </div>

  <div class="abs card" style="top:513px">
    <div class="card-head">Prairie Country Auction-GUNS-COINS-ANTIQUES</div>
    <div class="abs card-photo" role="img" aria-label="Photo of a single-storey house with a garage"></div>
    <div class="abs btn" style="left:32px"><i></i>Details</div>
    <div class="abs btn" style="left:116px"><i></i>Photos</div>
    <div class="abs card-info">
      <div class="card-date">Thursday, August 21st at 10:00 A.M.</div>
      <div class="card-desc">Selling 3120 Acres of land in tracts of 2590 Acres&amp; 560 Acres</div>
      <div class="card-bill">Click here to view Sale Bill!</div>
      <div class="mono"><b>LIVE OFF-SITE AUCTION</b><br><b>Auction Location:</b><br><svg class="pin" width="7" height="9" viewBox="0 0 7 9"><path d="M3.5 0a3.2 3.2 0 0 0-3.2 3.2C.3 5.5 3.5 9 3.5 9s3.2-3.5 3.2-5.8A3.2 3.2 0 0 0 3.5 0z" fill="#c41424"/></svg>118 N Main St, Elmdale, OK 73900<br><b>Property Location:</b><br><svg class="pin" width="7" height="9" viewBox="0 0 7 9"><path d="M3.5 0a3.2 3.2 0 0 0-3.2 3.2C.3 5.5 3.5 9 3.5 9s3.2-3.5 3.2-5.8A3.2 3.2 0 0 0 3.5 0z" fill="#c41424"/></svg>118 N Main St, Elmdale, OK 73900<br><b>Begins:</b> 08/21/14 at 10:00 AM CDT</div>
    </div>
  </div>

  <div class="abs card" style="top:740px">
    <div class="card-head">Prairie Country Auction-GUNS-COINS-ANTIQUES</div>
    <div class="abs card-photo" role="img" aria-label="Photo of a single-storey house with a garage"></div>
    <div class="abs btn" style="left:32px"><i></i>Details</div>
    <div class="abs btn" style="left:116px"><i></i>Photos</div>
    <div class="abs card-info">
      <div class="card-date">Thursday, August 21st at 10:00 A.M.</div>
      <div class="card-desc">Selling 3120 Acres of land in tracts of 2590 Acres&amp; 560 Acres</div>
      <div class="card-bill">Click here to view Sale Bill!</div>
      <div class="mono"><b>LIVE OFF-SITE AUCTION</b><br><b>Auction Location:</b><br><svg class="pin" width="7" height="9" viewBox="0 0 7 9"><path d="M3.5 0a3.2 3.2 0 0 0-3.2 3.2C.3 5.5 3.5 9 3.5 9s3.2-3.5 3.2-5.8A3.2 3.2 0 0 0 3.5 0z" fill="#c41424"/></svg>118 N Main St, Elmdale, OK 73900<br><b>Property Location:</b><br><svg class="pin" width="7" height="9" viewBox="0 0 7 9"><path d="M3.5 0a3.2 3.2 0 0 0-3.2 3.2C.3 5.5 3.5 9 3.5 9s3.2-3.5 3.2-5.8A3.2 3.2 0 0 0 3.5 0z" fill="#c41424"/></svg>118 N Main St, Elmdale, OK 73900<br><b>Begins:</b> 08/21/14 at 10:00 AM CDT</div>
    </div>
  </div>

  <div class="abs powered">powered by BidWorks.com</div>

  <aside class="abs widget" style="top:320px;height:143px">
    <div class="widget-head">Email signup</div>
    <div class="signup-copy">Please join our free mailing list to get auction alerts for upcoming events.</div>
    <div class="signup-input">Enter Your Email</div>
    <div class="signup-btn">Subscribe</div>
  </aside>

  <aside class="abs widget" style="top:487px;height:250px">
    <div class="widget-head">Featured Auctions</div>
    <div class="feat-title">ONLINE ONLY ABSOLUTE<br>AUCTION - PERSONAL<br>PROPERTY</div>
    <div class="feat-map" role="img" aria-label="Aerial map of the lots for sale"></div>
    <div class="feat-cap">LOTS 13 &amp; 14 FOR SALE,<br>MILLBROOK IOWA<br>Third Street, Millbrook, IA 52700</div>
  </aside>

  <div class="abs video">
    <div class="video-frame" role="img" aria-label="Featured video: auctioneer calling a sale to a crowd">
      <svg width="34" height="34" viewBox="0 0 34 34"><circle cx="17" cy="17" r="15" fill="rgba(255,255,255,.85)" stroke="#222" stroke-width="2"/><path d="M13 10l11 7-11 7z" fill="#222"/></svg>
    </div>
    <svg width="182" height="10" viewBox="0 0 182 10"><circle cx="5" cy="5" r="3" fill="#fff"/><rect x="12" y="4" width="120" height="2" fill="#555"/><rect x="150" y="3" width="26" height="4" fill="#777"/></svg>
  </div>

  <aside class="abs testimonial">
    <h3>Marla Quinlan</h3>
    <p>I met Pellow broken when I was looking for a way to auction my parent's household goods. Since I'm from Michigan I was completely unfamiliar with the auction process because it's not common here. Dale asked if I would let...</p>
    <div class="more">Read more ›</div>
  </aside>
</div>

<div class="abs footer-contact">Dale Pellow Broker &amp; Auctioneer<br>Email: dpellow@pellowmail.net<br>Mobile:&nbsp; 555-201-4470<br><div style="height:2px"></div>Owen Brantz<br>Sales Associate<br>Mobile: 555-201-8832</div>

<div class="badge" style="left:427px;top:1086px;width:58px;height:32px"></div>
<div class="badge" style="left:498px;top:1084px;width:32px;height:36px"></div>
<div class="badge" style="left:542px;top:1086px;width:34px;height:34px;border-radius:50%"></div>
<div class="badge" style="left:585px;top:1084px;width:32px;height:34px;border-radius:50%"></div>
<div class="badge" style="left:627px;top:1086px;width:60px;height:32px"></div>
<div class="badge" style="left:467px;top:1132px;width:62px;height:28px"></div>
<div class="badge" style="left:547px;top:1128px;width:30px;height:34px"></div>

<div class="abs footer-copy">Copyright © 2014 • Pellow Auction &amp; Real Estate. • All Rights Reserved</div>
<div class="abs footer-powered">Powered by: BidWorks.com &amp; Quillforge</div>
</body>
</html>
```